Post Disaster Temporary Housing Literature Review poster

Wanting a poster design for two Emergency Management conferences we have coming up. The information to be included in the poster is capturing the purpose, findings and recommendations from a post disaster temporary housing literature review looking at “What should government consider in order to improve planning and decision making for accommodation needs after a disaster, and to support people’s transition to stable housing?”
I’d like to enhance the visual appeal through including relevant images or graphic. I am also open to reducing the text if needed.
The government group I work with focuses on the social and human side of disaster recovery so keen for any images to reflect the human aspect and not focus solely on disasters or housing.
Government and NGO's

```html
<!DOCTYPE html>
<html lang="en">
<head>
<meta charset="utf-8">
<title>Post Disaster Temporary Housing Conference</title>
<link rel="stylesheet" href="https://fonts.googleapis.com/css2?family=Poppins:wght@400;500;600;700;800&display=swap">
<style>
  :root {
    --brand-blue: #1f4f9f;
    --navy: #14243f;
    --body-text: #222a36;
    --paper: #ffffff;
    --dust-light: #d8b28a;
    --dust-mid: #a8764c;
    --dust-dark: #4b3526;
  }
  * { box-sizing: border-box; margin: 0; padding: 0; }
  html, body { width: 849px; height: 1200px; overflow: hidden; background: var(--paper); }
  .poster {
    position: relative;
    width: 849px;
    height: 1200px;
    overflow: hidden;
    background: var(--paper);
    font-family: "Poppins", sans-serif;
    color: var(--body-text);
  }
  .hero-photo {
    position: absolute;
    left: 57px; top: 0;
    width: 404px; height: 515px;
    background:
      radial-gradient(ellipse at 70% 30%, rgba(255,220,170,.55), transparent 60%),
      linear-gradient(160deg, var(--dust-light) 0%, var(--dust-mid) 50%, var(--dust-dark) 100%);
  }
  .conference-title {
    position: absolute;
    left: 505px; top: 72px;
    width: 340px;
    font-weight: 700;
    font-size: 55px;
    line-height: 83px;
    color: var(--brand-blue);
  }
  .research-question {
    position: absolute;
    left: 57px; top: 526px;
    width: 780px;
    font-weight: 700;
    font-size: 20px;
    line-height: 44px;
    color: var(--navy);
  }
  .purpose-heading {
    position: absolute;
    left: 57px; top: 660px;
    font-weight: 600;
    font-size: 30px;
    line-height: 1.2;
    color: var(--brand-blue);
  }
  .body-copy {
    position: absolute;
    left: 57px;
    width: 745px;
    font-size: 15.5px;
    line-height: 25px;
    text-align: justify;
  }
  .purpose-copy { top: 710px; }
  .credit-copy { top: 905px; }
  .subheading {
    position: absolute;
    left: 57px; top: 866px;
    font-weight: 700;
    font-size: 18px;
    line-height: 1.2;
    color: var(--navy);
  }
  .next-list {
    position: absolute;
    left: 57px; top: 1012px;
    list-style: none;
  }
  .next-list li {
    display: flex;
    align-items: center;
    gap: 16px;
    font-weight: 700;
    font-size: 22px;
    color: var(--navy);
    height: 40px;
    margin-bottom: 17px;
  }
  .next-list svg { width: 30px; height: 30px; flex: none; }
  .partner-name {
    position: absolute;
    left: 325px; top: 1072px;
    display: flex;
    align-items: center;
    gap: 12px;
    font-weight: 500;
    font-size: 15px;
    line-height: 1.3;
    color: var(--brand-blue);
    width: 230px;
  }
  .partner-name .mark {
    width: 34px; height: 34px;
    border-radius: 50%;
    background: var(--brand-blue);
    flex: none;
  }
  .corner-disc {
    position: absolute;
    left: 608px; top: 1000px;
    width: 400px; height: 400px;
    border-radius: 50%;
    background: var(--brand-blue);
  }
  .poster-code {
    position: absolute;
    right: 22px; bottom: 20px;
    font-weight: 600;
    font-size: 15px;
    color: var(--paper);
  }
</style>
</head>
<body>
<main class="poster">
  <div class="hero-photo" role="img" aria-label="Photograph of rescue workers in hard hats searching through dusty rubble of a collapsed building"></div>

  <h1 class="conference-title">Post<br>Disaster<br>Temporary<br>Housing<br>Conference</h1>

  <h2 class="research-question">What Should Government Consider In Order To Improve Planning<br>And Decision Making For Accommodation Needs After A Disaster,<br>And To Support People’s Transition To Stable Housing?</h2>

  <h3 class="purpose-heading">Purpose</h3>
  <p class="body-copy purpose-copy">There are currently significant challenges in supporting displaced people with timely and equitable access to emergency and temporary accommodation and assisting them on a path to stable housing in the aftermath of a disaster. This report seeks to support agencies and decision makers to formulate and implement appropriate approaches to post-disaster housing, factoring in the scale of a disaster and varying community cohorts.</p>

  <p class="subheading">The central research question underpinning this report is:</p>
  <p class="body-copy credit-copy">The full report was commissioned by the Recovery Wellbeing Network (RWN) and undertaken by Helen Marlowe and Peter Aldine through the Southern Coast Institute of Technology (SCIT). The findings and recommendations may be utilised by stakeholders.</p>

  <ul class="next-list">
    <li><svg viewBox="0 0 30 30" aria-hidden="true"><circle cx="15" cy="15" r="15" fill="#1f4f9f"/><path d="M8.5 15.5l4.5 4.5 8.5-9" fill="none" stroke="#fff" stroke-width="3" stroke-linecap="round" stroke-linejoin="round"/></svg>Findings</li>
    <li><svg viewBox="0 0 30 30" aria-hidden="true"><circle cx="15" cy="15" r="15" fill="#1f4f9f"/><path d="M8.5 15.5l4.5 4.5 8.5-9" fill="none" stroke="#fff" stroke-width="3" stroke-linecap="round" stroke-linejoin="round"/></svg>Recommendations</li>
    <li><svg viewBox="0 0 30 30" aria-hidden="true"><circle cx="15" cy="15" r="15" fill="#1f4f9f"/><path d="M8.5 15.5l4.5 4.5 8.5-9" fill="none" stroke="#fff" stroke-width="3" stroke-linecap="round" stroke-linejoin="round"/></svg>Next Steps</li>
  </ul>

  <div class="partner-name"><span class="mark" aria-hidden="true"></span><span>Recovery Wellbeing Network</span></div>

  <div class="corner-disc" aria-hidden="true"></div>
  <span class="poster-code">C47</span>
</main>
</body>
</html>
```